VFX Company Business Card Design Project

The Kestrel Works is a decentralized Visual Effects Studio servicing the television and feature film industries.
Project Brief:
Take our logo that was previously designed on Pencil Harbor and make a double sided business card.
Requirements:
- Card MUST be double sided.
- Front of card MUST have the yellow part of our logo against the dark grey background.
- Back of card is completely up to the designer.
- Back of card must include the complete company logo.
Please follow these File Preparation guidelines:
http://printnook.ca/infopage?file=filetype_en&s=PrintNook_new&lang=en
Business

```html
<!DOCTYPE html>
<html lang="en">
<head>
<meta charset="utf-8">
<title>The Kestrel Works — Business Card</title>
<link href="https://fonts.googleapis.com/css2?family=Jost:ital,wght@0,300;0,400;0,500;1,600&family=Source+Sans+3:wght@400&display=swap" rel="stylesheet">
<style>
  :root {
    --backdrop: #e6d8c8;
    --card: #2b2b2b;
    --slate: #5e6b70;
    --rule: #f2f2f2;
    --gold: #f7c325;
    --text-light: #ffffff;
    --text-soft: #d6d6d6;
    --label: #1f1f1f;
  }
  * { margin: 0; padding: 0; box-sizing: border-box; }
  html, body { width: 1200px; height: 788px; overflow: hidden; }
  body {
    position: relative;
    background: var(--backdrop);
    font-family: "Jost", "Futura", sans-serif;
    color: var(--text-light);
  }

  .side-label {
    position: absolute;
    width: 200px;
    text-align: center;
    font-family: "Source Sans 3", "Myriad Pro", sans-serif;
    font-size: 22px;
    color: var(--label);
  }
  .side-label--back { left: 500px; top: 32px; }
  .side-label--front-one { left: 227px; top: 403px; }
  .side-label--front-two { left: 800px; top: 403px; }

  .card {
    position: absolute;
    width: 524px;
    height: 300px;
    border-radius: 22px;
    background: var(--card);
    overflow: hidden;
    box-shadow: 0 4px 10px rgba(0,0,0,0.25);
  }
  .card--back { left: 338px; top: 78px; }
  .card--front-one { left: 55px; top: 446px; }
  .card--front-two { left: 623px; top: 446px; }

  /* back side */
  .edge-band {
    position: absolute; left: 0; top: 0;
    width: 62px; height: 100%;
    background: var(--slate);
  }
  .edge-rule {
    position: absolute; left: 65px; top: 0;
    width: 4px; height: 100%;
    background: var(--rule);
  }
  .wordmark {
    position: absolute;
    font-weight: 500;
    letter-spacing: 0.5px;
    white-space: nowrap;
    line-height: 1;
  }
  .card--back .wordmark {
    left: 92px; top: 48px;
    font-size: 38px;
    color: var(--slate);
  }
  .holder {
    position: absolute; left: 91px; top: 148px;
    font-weight: 300;
    font-size: 20px;
    color: var(--text-soft);
    letter-spacing: 0.5px;
  }
  .holder__role { font-size: 14px; }
  .contact-list {
    position: absolute; left: 90px; top: 184px;
    list-style: none;
    font-size: 14px;
    line-height: 22px;
  }
  .contact-list b { font-weight: 600; font-style: italic; }
  .address {
    position: absolute; left: 259px; top: 214px;
    padding-left: 9px;
    border-left: 1px solid #8a8a8a;
    font-size: 13px;
    line-height: 18px;
    color: var(--text-light);
  }

  /* front sides */
  .card--front-one .wordmark {
    left: 0; width: 100%; top: 118px;
    text-align: center;
    font-size: 52px;
    color: var(--gold);
  }
  .mark-dot {
    position: absolute; left: 52px; top: 126px;
    width: 46px; height: 46px;
    border-radius: 50%;
    background: var(--gold);
  }
  .card--front-two .wordmark {
    left: 116px; top: 130px;
    font-size: 38px;
    color: var(--slate);
  }
  .site {
    position: absolute; left: 0; width: 100%; top: 256px;
    text-align: center;
    font-size: 20px;
    letter-spacing: 3.5px;
    color: var(--text-light);
  }
</style>
</head>
<body>

  <p class="side-label side-label--back">Back</p>
  <section class="card card--back">
    <div class="edge-band"></div>
    <div class="edge-rule"></div>
    <p class="wordmark">The Kestrel Works</p>
    <p class="holder">Your Name, <span class="holder__role">Designation</span></p>
    <ul class="contact-list">
      <li><b>cell</b> 123-456-7890</li>
      <li><b>phone</b> 123-456-7890</li>
      <li><b>email</b> info@kestrelworks.com</li>
      <li><b>web</b> www.kestrelworks.com</li>
    </ul>
    <address class="address" style="font-style:normal">
      0000#, Area Name<br>
      Street Name<br>
      State Name, Country code
    </address>
  </section>

  <p class="side-label side-label--front-one">Front - 1</p>
  <section class="card card--front-one">
    <p class="wordmark">The Kestrel Works</p>
    <p class="site">www.kestrelworks.com</p>
  </section>

  <p class="side-label side-label--front-two">Front - 2</p>
  <section class="card card--front-two">
    <div class="mark-dot"></div>
    <p class="wordmark">The Kestrel Works</p>
    <p class="site">www.kestrelworks.com</p>
  </section>

</body>
</html>
```